Modern Banner and Window Decal Design For Law Firm Lawyer

We are looking for three modern and sophisticated banner design and window decal for our law firm.

Banner measurements/types:

1) Height: 130 cm Width: 160 cm (Outdoor banner)
2) Height: 200 cm Width: 85 cm (Pull up/retractable indoor banner)

Window Decal:
3) Height: 70cm width 70cm

Our law firm is based in Melbourne, Australia and we deal with property law mostly.

We prefer a white background with classic text in black or grey. We would also like a dash of colour so please use a green, blue or aqua colour palette that is consistent with our logo. Vector attached. A nice photo of property, Melbourne city viee, or family home would be nice.

We do not want any law related images - scales of justice, gavel or the like.

Our ultimate goal is to communicate that the firm is modern, professional and knowledgeable

We would like the following:

1. Our logo
2. Our services: - Property Law - Wills - Powers of Attorney - Probate - Estate Administration - Consultancy & Agency
3. Phone number
4. Web Address

5. For pull up/retractable banner we would also like the following text:

We use the latest digital technology and fixed-fees to provide fast and affordable legal advice that is easy to understand.

For privacy reasons, we will provide business details once we have decided on the winner.

We will monitor entries closely and promise to provide feedback and guidance on each entry.

Thank you very much for considering this project.

Target Market(s)

General public, professionals, lawyers and conveyancers

Industry/Entity Type

Law Firm

Font styles to use
Sans Serif

Colors
0393ce
34a6d7
0456a4
3176b5
acd037
33b8a4
86cfc6
00a990
9ccb3b

Requirements
Must have
• 1. Our logo
• 2. Our services: - Property Law - Wills - Powers of Attorney - Probate & Estate Administration - Consultancy & Agency
• 3. Phone number
• 4. Web Address
Nice to have
• Picture of Melbourne, Australia city ; property/buildings/lawyers
Should not have
• We do not want any law related images - scales of justice, gavel or the like.

```html
<!DOCTYPE html>
<html lang="en">
<head>
<meta charset="utf-8">
<title>Ridgeview Legal – Pull-up Banner</title>
<link href="https://fonts.googleapis.com/css2?family=Montserrat:wght@500;700;800&family=Oswald:wght@400;500&family=Roboto:wght@500&display=swap" rel="stylesheet">
<style>
  :root {
    --page-bg: #e9eaec;
    --navy-blue: #0456a4;
    --bright-blue: #0a6cc0;
    --sky-blue: #34a6d7;
    --teal: #33b8a4;
    --ink: #111418;
    --ink-soft: #3a3f45;
    --panel-light: #f4f4f4;
    --panel-shade: #d8d9db;
  }
  * { box-sizing: border-box; margin: 0; padding: 0; }
  html, body { width: 1200px; height: 1000px; overflow: hidden; }
  body { background: var(--page-bg); position: relative; font-family: "Montserrat", sans-serif; }

  .banner {
    position: absolute; left: 405px; top: 30px;
    width: 390px; height: 940px; overflow: hidden;
    box-shadow: 0 6px 24px rgba(0,0,0,.18);
  }
  .banner-art { position: absolute; inset: 0; }

  .brand {
    position: absolute; left: 34px; top: 52px;
    display: flex; align-items: center; gap: 14px;
  }
  .brand-dot { width: 64px; height: 64px; border-radius: 50%; background: var(--teal); }
  .brand-name {
    font-family: "Montserrat", sans-serif; font-weight: 500;
    color: var(--ink-soft); line-height: 1.05; letter-spacing: .5px;
  }
  .brand-name .line-1 { display: block; font-size: 29px; }
  .brand-name .line-2 { display: block; font-size: 22px; letter-spacing: 1.5px; }

  .services-title {
    position: absolute; left: 72px; top: 528px;
    width: 224px; height: 32px;
    background: var(--navy-blue); color: #fff;
    border-radius: 8px;
    font-weight: 700; font-size: 22px; letter-spacing: .3px;
    display: flex; align-items: center; justify-content: center;
  }

  .services-list {
    position: absolute; left: 62px; top: 572px; width: 310px;
    list-style: none;
    font-family: "Oswald", sans-serif; font-weight: 500;
    font-size: 26px; line-height: 28px; color: var(--ink);
    text-transform: uppercase;
  }
  .services-list li { position: relative; padding-left: 24px; margin-bottom: 9px; }
  .services-list li::before {
    content: ""; position: absolute; left: 0; top: 8px;
    width: 12px; height: 12px; background: var(--bright-blue);
  }

  .tagline {
    position: absolute; left: 50px; top: 790px; width: 284px;
    border: 1.5px solid var(--navy-blue); border-radius: 3px;
    background: #fff;
    padding: 3px 6px;
    font-family: "Oswald", sans-serif; font-weight: 400;
    font-size: 11.5px; line-height: 17px; color: var(--ink);
    text-align: center;
  }

  .phone {
    position: absolute; left: 0; right: 0; top: 845px;
    display: flex; align-items: center; justify-content: center; gap: 8px;
    font-family: "Oswald", sans-serif; font-weight: 500;
    font-size: 30px; color: var(--ink);
  }
  .phone-icon { width: 26px; height: 26px; }

  .web-address {
    position: absolute; left: 0; right: 0; top: 884px;
    text-align: center;
    font-family: "Roboto", sans-serif; font-weight: 500;
    font-size: 15px; color: var(--ink);
  }
</style>
</head>
<body>
  <div class="banner">
    <svg class="banner-art" viewBox="0 0 390 940" width="390" height="940" aria-hidden="false">
      <defs>
        <linearGradient id="cityPhoto" x1="0" y1="0" x2="0.35" y2="1">
          <stop offset="0" stop-color="#8fbde6"/>
          <stop offset="0.22" stop-color="#b7cfe2"/>
          <stop offset="0.3" stop-color="#6d8494"/>
          <stop offset="0.55" stop-color="#7c8079"/>
          <stop offset="0.78" stop-color="#8d8f8a"/>
          <stop offset="1" stop-color="#d8c6a2"/>
        </linearGradient>
        <linearGradient id="lowerPanel" x1="0" y1="0" x2="0" y2="1">
          <stop offset="0" stop-color="var(--panel-light)"/>
          <stop offset="1" stop-color="var(--panel-shade)"/>
        </linearGradient>
      </defs>
      <rect class="city-photo" x="0" y="0" width="390" height="560" fill="url(#cityPhoto)"
            role="img" aria-label="Aerial photo of a coastal city skyline with a tall tower, river and beach"/>
      <path class="lower-panel" d="M0 455 C100 510 250 548 390 532 L390 940 L0 940 Z" fill="url(#lowerPanel)"/>
      <path class="swoosh-dark" d="M0 418 C90 488 240 533 390 514 L390 532 C250 548 100 512 0 458 Z" fill="var(--bright-blue)"/>
      <path class="swoosh-light" d="M0 440 C95 500 240 538 390 522" fill="none" stroke="var(--sky-blue)" stroke-width="3" opacity=".7"/>
    </svg>

    <div class="brand">
      <span class="brand-dot"></span>
      <span class="brand-name"><span class="line-1">RIDGEVIEW</span><span class="line-2">LEGAL</span></span>
    </div>

    <div class="services-title">OUR SERVICES:</div>

    <ul class="services-list">
      <li>Property Law</li>
      <li>Wills</li>
      <li>Powers of Attorney</li>
      <li>Probate &amp; Estate<br>Administration</li>
      <li>Consultancy &amp; Agency</li>
    </ul>

    <p class="tagline">We use the latest digital technology and fixed-fees to provide fast and affordable legal advice that is easy to understand.</p>

    <div class="phone">
      <svg class="phone-icon" viewBox="0 0 26 26" aria-hidden="true">
        <rect width="26" height="26" rx="5" fill="var(--bright-blue)"/>
        <path d="M8.2 5.5c.6-.3 1.3-.1 1.6.5l1.4 2.8c.3.6.1 1.2-.4 1.6l-1.2.9c.9 1.9 2.3 3.3 4.2 4.2l.9-1.2c.4-.5 1-.7 1.6-.4l2.8 1.4c.6.3.8 1 .5 1.6l-.8 1.6c-.4.8-1.3 1.2-2.2 1-5.1-1.1-9-5-10.1-10.1-.2-.9.2-1.8 1-2.2z" fill="#fff"/>
      </svg>
      <span>555-0142-7788</span>
    </div>

    <div class="web-address">www.ridgeviewlegal.com</div>
  </div>
</body>
</html>
```